Vantro cards

I am in the auto motive, transportation business I would like a business card that is Something cool, modern edgy, having to do with car culture. I offer towing service for high and exotic cars. I also provide towing for collisions and car accidents. I offer open and enclosed transport nationwide.

Target Market(s)

Car culture people high end auto collectors

Industry/Entity Type

Towing car carrier

Contact Information for Business Card

My company colors black yellow and silver

Font styles to use
Serif

```html
<!DOCTYPE html>
<html lang="en">
<head>
<meta charset="utf-8">
<title>Vantro Transportation – Business Card</title>
<link rel="stylesheet" href="https://fonts.googleapis.com/css2?family=Arimo:wght@400;700&display=swap">
<style>
  :root {
    --stage: #151515;
    --card: #1e1e1f;
    --yellow: #fbe05a;
    --silver: #c3c3c6;
    --white: #f2f2f2;
  }
  * { margin: 0; padding: 0; box-sizing: border-box; }
  html, body { width: 1200px; height: 900px; overflow: hidden; background: var(--stage); }
  .stage { position: relative; width: 1200px; height: 900px; }
  .card {
    position: absolute; left: 100px; top: 164px;
    width: 1000px; height: 572px;
    background: var(--card);
    border-radius: 30px;
    overflow: hidden;
    font-family: "Arimo", Arial, sans-serif;
  }
  .card__swoosh { position: absolute; inset: 0; width: 100%; height: 100%; }
  .brand {
    position: absolute; left: 90px; top: 170px;
    width: 290px; text-align: center;
  }
  .brand__name {
    font-weight: 700; font-size: 72px; letter-spacing: 3px;
    color: var(--silver); line-height: 1;
  }
  .divider {
    position: absolute; left: 425px; top: 150px;
    width: 1.5px; height: 270px; background: var(--yellow);
  }
  .contact {
    position: absolute; left: 465px; top: 150px;
    color: var(--white); font-size: 22px; line-height: 1.38;
  }
  .contact__name {
    color: var(--yellow); font-weight: 700; font-size: 31px;
    letter-spacing: 1.5px; text-transform: uppercase; line-height: 1.1;
  }
  .contact__title { margin-bottom: 2px; }
  .contact__address { margin-bottom: 6px; }
  .contact__row { display: flex; align-items: center; gap: 12px; }
  .contact__icon { width: 18px; height: 18px; flex: none; }
</style>
</head>
<body>
<main class="stage">
  <section class="card" aria-label="Vantro Transportation business card">
    <svg class="card__swoosh" viewBox="0 0 1000 572" preserveAspectRatio="none" aria-hidden="true">
      <path d="M0,300 C190,440 500,525 800,572 L740,572 C460,526 170,440 0,308 Z" fill="var(--silver)"/>
      <path d="M0,308 C170,440 460,526 740,572" fill="none" stroke="var(--card)" stroke-width="8"/>
      <path d="M0,318 C160,448 440,530 720,572 L0,572 Z" fill="var(--yellow)"/>
    </svg>

    <div class="brand">
      <p class="brand__name">VANTRO</p>
    </div>

    <div class="divider"></div>

    <div class="contact">
      <p class="contact__name">Dorian Kessler</p>
      <p class="contact__title">CEO/Founder</p>
      <p class="contact__address">P.O. Box 3870 Street<br>Country Name AB 6127</p>
      <p class="contact__row">
        <svg class="contact__icon" viewBox="0 0 24 24" aria-hidden="true"><path fill="var(--yellow)" d="M6.6 10.8a15 15 0 0 0 6.6 6.6l2.2-2.2a1 1 0 0 1 1-.25 11.4 11.4 0 0 0 3.6.57 1 1 0 0 1 1 1V20a1 1 0 0 1-1 1A17 17 0 0 1 3 4a1 1 0 0 1 1-1h3.5a1 1 0 0 1 1 1c0 1.25.2 2.45.57 3.57a1 1 0 0 1-.25 1z"/></svg>
        (555) 318 4402
      </p>
      <p class="contact__row">
        <svg class="contact__icon" viewBox="0 0 24 24" aria-hidden="true"><rect x="6" y="2" width="12" height="20" rx="2" fill="none" stroke="var(--yellow)" stroke-width="2"/><circle cx="12" cy="18" r="1.2" fill="var(--yellow)"/></svg>
        (555) 827 1169
      </p>
      <p class="contact__row">
        <svg class="contact__icon" viewBox="0 0 24 24" aria-hidden="true"><rect x="2" y="5" width="20" height="14" rx="1.5" fill="var(--yellow)"/><path d="M2.5 6l9.5 7 9.5-7" fill="none" stroke="var(--card)" stroke-width="1.6"/></svg>
        info@vantrotransport.com
      </p>
      <p class="contact__row">
        <svg class="contact__icon" viewBox="0 0 24 24" aria-hidden="true"><g fill="none" stroke="var(--yellow)" stroke-width="1.8"><circle cx="12" cy="12" r="9.5"/><ellipse cx="12" cy="12" rx="4.2" ry="9.5"/><path d="M2.5 12h19M4 7h16M4 17h16"/></g></svg>
        www.vantrotransport.com
      </p>
    </div>
  </section>
</main>
</body>
</html>
```